Website Design Needed for Performance Horse Trading Business

We require a website designed for Saddlewend, a new business which lists top quality performance stock horse bloodlines for sale. Our Australian company caters to the Australian Stock Horse, Quarter Horse and Paint Horse breeds of horse used for performance events such as Camp drafting and Cutting. The website design needs to communicate quality, have a professional look while maintaining a western, rural feel.
Colour schemes that we are looking for are either grey and orange, navy and grey or brown and grey.
The logo for the website has been attached below
Design deliverables are as follows:
-Main Page
-Horses for Sale Page
-Horse Listing Page
-Html & CSS files for pages
MAIN PAGE
----------------
Description: This page is where customers land, search for horses, see premium horses
Elements which need to be included on the main page are
-a horse filter section, allowing customers to search for horse listings by filtering attributes.
-premium listings displaying large photos of horse, price and location.
Horses for Sale PAGE
---------------------------------
Description: This page displays a list of available horses for sale as per the filtered results.
Elements which need to be included on this page are
- a filter panel which allows customers to filter results
- list of horses available for sale
Horse Listing Page
-------------------------------
Description: This page displays all the information about the horse for sale.
Screenshots of the basic program are attached for the Horses for Sale Page and the Horse Listing Page to give an idea of the elements required ONLY and should not be thought of as a design guideline.
Webpage HEADER
-------------------------
The Header section of the website should include login/signup buttons, 'my account' buttons (or links) as well as a featured link/button that says 'Sell Your Horse'
Updates
Thank you all for your designs so far. We would like to see the Sell Your Horse section featured more in the website design to attract customers. This would be as a button or highlighted link that is eye catching in the primary section of the website design of the main page. Perhaps placing it on the right hand side adjacent to the search function lets customers make the mental decision as to whether they are looking to buy or looking to sell when they visit the website. The wording above or near the button would be 'Advertise your horse with us' with the words on the button being 'Create Ad!'.
Industry/Entity Type
Events
Look and feel
Each slider illustrates characteristics of the customer's brand and the style your logo design should communicate.

```html
<!DOCTYPE html>
<html lang="en">
<head>
<meta charset="utf-8">
<title>Saddlewend – Performance Stock Horses</title>
<link href="https://fonts.googleapis.com/css2?family=Arimo:wght@400;700&display=swap" rel="stylesheet">
<style>
:root{
  --paper:#f1ede5;
  --ink:#1e1a18;
  --dark:#2a211e;
  --orange:#e0870c;
  --muted:#6e6a66;
  --white:#ffffff;
  --line:#d9d3c8;
}
*{box-sizing:border-box;margin:0;padding:0}
html,body{width:772px;height:1200px;overflow:hidden}
body{background:var(--paper);font-family:"Arimo",Arial,sans-serif;color:var(--ink);position:relative}
.abs{position:absolute}
.brand{font-size:24px;font-weight:700;letter-spacing:-.5px;color:var(--dark);display:flex;align-items:center;gap:6px}
.brand .dot{width:10px;height:10px;border-radius:50%;background:var(--dark)}
.header-brand{left:84px;top:10px}
.btn{display:flex;align-items:center;justify-content:center;font-size:10px;color:var(--white);text-transform:uppercase}
.btn-login{left:522px;top:9px;width:74px;height:26px;background:var(--dark)}
.btn-account{left:613px;top:9px;width:74px;height:26px;background:var(--orange)}
.sell-link{right:84px;top:46px;font-size:10px;text-decoration:underline;color:var(--ink)}
.nav{left:0;top:66px;width:772px;height:51px;background:var(--dark);display:flex;align-items:center;justify-content:space-between;padding:0 85px 0 84px}
.nav a{font-size:9.5px;color:var(--white);text-decoration:none}
.nav a.active{color:var(--orange)}
.hero{left:0;top:117px;width:772px;height:337px;background:radial-gradient(ellipse at 50% 55%,#b3703f 0%,#9a6540 28%,#cdbea6 60%,#e3dccd 100%)}
.hero-arrow{top:272px}
.search-band{left:0;top:454px;width:772px;height:80px;background:var(--dark)}
.field{top:480px;height:32px;width:216px;background:var(--white);font-size:9px;color:var(--muted);display:flex;align-items:center;padding-left:9px}
.btn-search{left:553px;top:480px;width:134px;height:32px;background:var(--orange);font-size:12.5px;text-transform:none}
.section-title{font-size:17.5px;color:var(--ink)}
.listing{top:595px;width:186px;height:271px;background:var(--white);border-top:3px solid var(--orange);border-bottom:3px solid var(--orange)}
.listing .photo{height:150px;width:100%}
.listing .body{padding:12px 11px 0}
.listing h3{font-size:12.5px;font-weight:400;color:var(--orange)}
.listing .meta{font-size:10px;margin-top:9px}
.listing p{font-size:8.6px;line-height:16px;color:var(--muted);margin-top:6px}
.event{top:928px;width:288px;height:160px;background:var(--white);padding:14px 13px}
.event .thumb{position:absolute;left:13px;top:14px;width:68px;height:60px}
.event .intro{margin-left:79px}
.event h3{font-size:12px;font-weight:400;color:var(--orange);margin-bottom:5px}
.event p{font-size:8.6px;line-height:16px;color:var(--muted)}
.event .more{font-size:8.6px;color:var(--orange);margin-top:5px}
.footer{left:0;top:1126px;width:772px;height:74px;background:var(--dark)}
.footer-brand{left:85px;top:1146px;color:var(--white);font-size:20px}
.footer-brand .dot{background:var(--white)}
.copyright{right:84px;top:1144px;font-size:8.6px;color:var(--white)}
.social{top:1166px;width:20px;height:20px;border-radius:50%;background:var(--white)}
</style>
</head>
<body>
<header>
  <div class="abs brand header-brand"><span class="dot"></span>SADDLEWEND</div>
  <a class="abs btn btn-login">Login</a>
  <a class="abs btn btn-account">My Account</a>
  <a class="abs sell-link">SELL YOUR HORSE</a>
  <nav class="abs nav">
    <a class="active">HOME</a><a>ABOUT US</a><a>OUR SERVICES</a><a>GALLERY</a><a>LATEST NEWS</a><a>BLOG</a><a>CONTACT US</a>
  </nav>
</header>

<section>
  <div class="abs hero" role="img" aria-label="Two bay horses galloping across an open paddock"></div>
  <svg class="abs hero-arrow" style="left:14px" width="25" height="25" viewBox="0 0 25 25"><circle cx="12.5" cy="12.5" r="11" fill="none" stroke="#fff" stroke-width="1.5" opacity=".8"/><path d="M14.5 7l-5 5.5 5 5.5" fill="none" stroke="#fff" stroke-width="2"/></svg>
  <svg class="abs hero-arrow" style="left:734px" width="25" height="25" viewBox="0 0 25 25"><circle cx="12.5" cy="12.5" r="11" fill="none" stroke="#fff" stroke-width="1.5" opacity=".8"/><path d="M10.5 7l5 5.5-5 5.5" fill="none" stroke="#fff" stroke-width="2"/></svg>
</section>

<section>
  <div class="abs search-band"></div>
  <div class="abs field" style="left:85px">List by category</div>
  <div class="abs field" style="left:319px">Keyword</div>
  <a class="abs btn btn-search">Search now !</a>
</section>

<section>
  <h2 class="abs section-title" style="left:83px;top:558px">Premium Listing</h2>
  <svg class="abs" style="left:656px;top:561px" width="32" height="14" viewBox="0 0 32 14"><circle cx="7" cy="7" r="6.5" fill="#e0870c"/><path d="M8.3 4.3L5.6 7l2.7 2.7" fill="none" stroke="#fff" stroke-width="1.5"/><circle cx="25" cy="7" r="6.5" fill="#e0870c"/><path d="M23.7 4.3L26.4 7l-2.7 2.7" fill="none" stroke="#fff" stroke-width="1.5"/></svg>

  <article class="abs listing" style="left:85px">
    <div class="photo" role="img" aria-label="Chestnut Quarter Horse leaning over a rail fence" style="background:linear-gradient(160deg,#9fa77a,#b5773a 55%,#5e4a33)"></div>
    <div class="body"><h3>Quarter Horse</h3><div class="meta">Price : $14,500 &nbsp;Location : Australia</div><p>Summo alterum luptatum at mei, everti singulis et eos, singulis moderatius per ea. Dolorem antiopam cum.</p></div>
  </article>
  <article class="abs listing" style="left:293px">
    <div class="photo" role="img" aria-label="Buckskin Australian Stock Horse with a red halter" style="background:linear-gradient(170deg,#b8c3c2,#a8845a 45%,#8c6a44)"></div>
    <div class="body"><h3>Australian Stock Horse</h3><div class="meta">Price : $14,500 &nbsp;Location : Australia</div><p>Summo alterum luptatum at mei, everti singulis et eos, singulis moderatius per ea. Dolorem antiopam cum.</p></div>
  </article>
  <article class="abs listing" style="left:501px">
    <div class="photo" role="img" aria-label="Three stock horses standing in a dry paddock" style="background:linear-gradient(180deg,#dcdcd6,#4a3a2e 50%,#8a7a4e)"></div>
    <div class="body"><h3>Australian Stock Horse</h3><div class="meta">Price : $14,500 &nbsp;Location : Australia</div><p>Summo alterum luptatum at mei, everti singulis et eos, singulis moderatius per ea. Dolorem antiopam cum.</p></div>
  </article>
</section>

<section>
  <h2 class="abs section-title" style="left:83px;top:890px">Performance Events</h2>
  <article class="abs event" style="left:85px">
    <div class="thumb" role="img" aria-label="Riders camp drafting on a green field" style="background:linear-gradient(180deg,#a9bfd0,#8d5a33 55%,#6f8a3c)"></div>
    <div class="intro"><h3>Camp Drafting</h3><p>Nulla expetenda contentiones mel at, autem dicta dicam in eam. Salutatus consequat deterruisset ut mei, nobis quodsi ornatus ad.</p></div>
    <p style="margin-top:3px">Mea ea iriure rationibus signiferumque, pro ut vidisse meliore mandamus. Cum ut nonumy pericula, nec ea virtute assueverit liberavisse virtute assueverit liberavisse.</p>
    <div class="more">read more...</div>
  </article>
  <article class="abs event" style="left:398px">
    <div class="thumb" role="img" aria-label="Grey horse being saddled for a cutting event" style="background:linear-gradient(150deg,#7a6a5c,#d8d8d8 55%,#6c6a6a)"></div>
    <div class="intro"><h3>Cutting</h3><p>Nulla expetenda contentiones mel at, autem dicta dicam in eam. Salutatus consequat deterruisset ut mei, nobis quodsi ornatus ad.</p></div>
    <p style="margin-top:3px">Mea ea iriure rationibus signiferumque, pro ut vidisse meliore mandamus. Cum ut nonumy pericula, nec ea virtute assueverit liberavisse virtute assueverit liberavisse.</p>
    <div class="more">read more...</div>
  </article>
</section>

<footer>
  <div class="abs footer"></div>
  <div class="abs brand footer-brand"><span class="dot"></span>SADDLEWEND</div>
  <div class="abs copyright">Copyright @ 2014 Saddlewend.All Rights Reserved.</div>
  <span class="abs social" style="left:621px"></span>
  <span class="abs social" style="left:644px"></span>
  <span class="abs social" style="left:668px"></span>
</footer>
</body>
</html>
```